Visitenkarten-Design für Garten- und Landschaftspflege
Nerapo Kulm setzte meine Vorstellungen absolut super um ich kann Ihn nur weiter empfehlen. vielen dank
Zielgruppe
Baumpflege, Baumfällung, Garten und Landschaftspflege meine zielgruppe sind Privatpersonen im alter von 20-100Jahren
Aufgabenstellung
Sehr geehrte Damen und Herren, die visitenkarte sollte die angaben so enthalten wie sie auf der von mir gestallteten Visitenkarten sind ( meine ist kein maß der Dinge). Ich habe mein Logo leider nur als 3.jpg Datei. Das Logo darf im Design erändert werden aber bitte nur Feinheiten ansonsten stehen ihnen alle türen offen um kreativ zu sein.
mit freundlichen Grüßen Jonas Vehmar

```html
<!DOCTYPE html>
<html lang="de">
<head>
<meta charset="utf-8">
<title>Visitenkarten Baumpflege Vehmar</title>
<link href="https://fonts.googleapis.com/css2?family=Mulish:wght@400;600;700&display=swap" rel="stylesheet">
<style>
:root{
  --olive:#465019;
  --olive-line:#3e4814;
  --lime:#bcd35f;
  --bright:#6cc241;
  --forest:#2f5a1c;
  --paper:#ffffff;
  --text:#3e4814;
}
*{margin:0;padding:0;box-sizing:border-box}
html,body{width:860px;height:1200px;overflow:hidden;background:#fff}
body{position:relative;font-family:'Mulish',sans-serif;color:var(--text)}
.card{position:absolute;width:302px;height:195px;background:var(--paper);box-shadow:4px 4px 7px rgba(0,0,0,.28);overflow:hidden}
.card--dark{background:var(--olive);color:#fff}
.col-left{left:96px}.col-right{left:429px}
.row-1{top:222px}.row-2{top:479px}.row-3{top:739px}
.stripes{position:absolute;left:0;width:100%;height:9px}
.stripes::before,.stripes::after{content:"";position:absolute;left:0;width:100%;background:var(--olive-line)}
.stripes::before{top:0;height:3px}.stripes::after{top:5px;height:4px}
.stripes--top{top:2px}.stripes--bottom{bottom:2px}
.card--dark .stripes::before,.card--dark .stripes::after{background:var(--lime)}
.card--dark .stripes--bottom::after{background:var(--olive-line)}
.brand{position:absolute;display:flex;align-items:center;justify-content:center;gap:6px;font-weight:700;white-space:nowrap;color:var(--olive)}
.brand__mark{width:10px;height:10px;background:currentColor}
.card--dark .brand{color:var(--lime)}
.brand--green{color:var(--forest)}
.brand--lg{font-size:19px;line-height:24px;left:0;right:0;top:86px}
.brand--band{font-size:17px;line-height:22px;left:0;right:0;top:84px}
.brand--sm{font-size:10px;line-height:14px;left:180px;width:112px;top:70px}
.services{position:absolute;list-style:none;font-size:7px;line-height:8.6px;left:14px;top:30px}
.services li::before{content:"· "}
.card--dark .services{font-size:9px;line-height:11px;top:32px}
.services--wide{font-size:8.4px;line-height:10px;left:99px;top:117px}
.person{position:absolute}
.person__name{font-size:12.6px;line-height:13px;letter-spacing:.3px}
.person__role{font-size:5.2px;line-height:6.6px;text-align:right}
.card--dark .person__role{color:var(--lime)}
.contact{position:absolute;font-size:8.6px;line-height:11px}
.contact div{display:flex;align-items:center;gap:2px;white-space:nowrap}
.contact .gap{margin-top:4.5px}
.contact svg{width:8px;height:8px;flex:none}
.contact .indent{padding-left:10px}
.rule{position:absolute;left:11px;right:11px;height:2px;background:var(--bright)}
</style>
</head>
<body>

<section class="card col-left row-1">
  <div class="stripes stripes--top"></div>
  <div class="brand brand--lg"><span class="brand__mark"></span>Baumpflege Vehmar</div>
  <div class="stripes stripes--bottom"></div>
</section>

<section class="card col-right row-1">
  <div class="stripes stripes--top"></div>
  <ul class="services">
    <li>Neupflanzungen</li>
    <li>Herstellung der Verkehrssicherheit von Bäumen</li>
    <li>Kronenrückschnitt (Einkürzung &amp; Kronenpflege)</li>
    <li>Prüfung von Bäumen auf Standsicherheit</li>
    <li>Fällung von Bäumen</li>
    <li>Obstbaumschnitt</li>
    <li>Wurzelstockfräsen</li>
  </ul>
  <div class="brand brand--sm"><span class="brand__mark"></span>Baumpflege Vehmar</div>
  <div class="person" style="left:14px;top:122px">
    <div class="person__name">Jonas Vehmar</div>
    <div class="person__role">Fachagrarwirt für Baumpflege<br>&amp; Baumsanierung</div>
  </div>
  <div class="contact" style="left:160px;top:121px">
    <div><svg viewBox="0 0 10 10"><path d="M5 9.5C3 7 2 5.5 2 4a3 3 0 0 1 6 0c0 1.5-1 3-3 5.5z" fill="none" stroke="currentColor"/></svg>Lindenweg 7</div>
    <div class="indent">85600 Grünau</div>
    <div class="gap"><svg viewBox="0 0 10 10"><rect x="3" y="1" width="4" height="8" rx="1" fill="currentColor"/></svg>0170 / 555 12 34</div>
    <div><svg viewBox="0 0 10 10"><rect x="1" y="2.5" width="8" height="5.5" fill="none" stroke="currentColor" stroke-width=".7"/><path d="M1 2.5l4 3 4-3" fill="none" stroke="currentColor" stroke-width=".7"/></svg>kontakt@baumpflege-vehmar.de</div>
    <div><svg viewBox="0 0 10 10"><circle cx="5" cy="5" r="4" fill="none" stroke="currentColor" stroke-width=".7"/><path d="M1 5h8M5 1c-2 2.5-2 5.5 0 8M5 1c2 2.5 2 5.5 0 8" fill="none" stroke="currentColor" stroke-width=".6"/></svg>baumpflege-vehmar.de</div>
  </div>
  <div class="stripes stripes--bottom"></div>
</section>

<section class="card card--dark col-left row-2">
  <div class="stripes stripes--top"></div>
  <div class="brand brand--lg"><span class="brand__mark"></span>Baumpflege Vehmar</div>
  <div class="stripes stripes--bottom"></div>
</section>

<section class="card card--dark col-right row-2">
  <div class="stripes stripes--top"></div>
  <ul class="services">
    <li>Neupflanzungen</li>
    <li>Baumschnitt</li>
    <li>Herstellung der Verkehrssicherheit<br>&nbsp;&nbsp;von Bäumen</li>
  </ul>
  <div class="brand brand--sm"><span class="brand__mark"></span>Baumpflege Vehmar</div>
  <div class="person" style="left:14px;top:122px">
    <div class="person__name">Jonas Vehmar</div>
    <div class="person__role">Fachagrarwirt für Baumpflege<br>&amp; Baumsanierung</div>
  </div>
  <div class="contact" style="left:160px;top:121px">
    <div><svg viewBox="0 0 10 10"><path d="M5 9.5C3 7 2 5.5 2 4a3 3 0 0 1 6 0c0 1.5-1 3-3 5.5z" fill="none" stroke="var(--lime)"/></svg>Lindenweg 7</div>
    <div class="indent">85600 Grünau</div>
    <div class="gap"><svg viewBox="0 0 10 10"><rect x="3" y="1" width="4" height="8" rx="1" fill="var(--lime)"/></svg>0170 / 555 12 34</div>
    <div><svg viewBox="0 0 10 10"><rect x="1" y="2.5" width="8" height="5.5" fill="none" stroke="var(--lime)" stroke-width=".7"/><path d="M1 2.5l4 3 4-3" fill="none" stroke="var(--lime)" stroke-width=".7"/></svg>kontakt@baumpflege-vehmar.de</div>
    <div><svg viewBox="0 0 10 10"><circle cx="5" cy="5" r="4" fill="none" stroke="var(--lime)" stroke-width=".7"/><path d="M1 5h8M5 1c-2 2.5-2 5.5 0 8M5 1c2 2.5 2 5.5 0 8" fill="none" stroke="var(--lime)" stroke-width=".6"/></svg>baumpflege-vehmar.de</div>
  </div>
  <div class="stripes stripes--bottom"></div>
</section>

<section class="card col-left row-3">
  <div class="rule" style="top:81px"></div>
  <div class="brand brand--band brand--green"><span class="brand__mark"></span>Baumpflege Vehmar</div>
  <div class="rule" style="top:106px"></div>
  <div class="person" style="left:11px;top:133px">
    <div class="person__name" style="font-size:10px;line-height:11px">Jonas Vehmar</div>
    <div class="person__role" style="text-align:left">Fachagrarwirt für Baumpflege<br>&amp; Baumsanierung</div>
  </div>
  <div class="contact" style="left:161px;top:131px">
    <div><svg viewBox="0 0 10 10"><path d="M5 9.5C3 7 2 5.5 2 4a3 3 0 0 1 6 0c0 1.5-1 3-3 5.5z" fill="none" stroke="var(--bright)"/></svg>Lindenweg 7</div>
    <div class="indent">85600 Grünau</div>
    <div class="gap"><svg viewBox="0 0 10 10"><rect x="3" y="1" width="4" height="8" rx="1" fill="var(--bright)"/></svg>0170 / 555 12 34</div>
    <div><svg viewBox="0 0 10 10"><rect x="1" y="2.5" width="8" height="5.5" fill="none" stroke="var(--bright)" stroke-width=".7"/><path d="M1 2.5l4 3 4-3" fill="none" stroke="var(--bright)" stroke-width=".7"/></svg>kontakt@baumpflege-vehmar.de</div>
    <div><svg viewBox="0 0 10 10"><circle cx="5" cy="5" r="4" fill="none" stroke="var(--bright)" stroke-width=".7"/><path d="M1 5h8M5 1c-2 2.5-2 5.5 0 8M5 1c2 2.5 2 5.5 0 8" fill="none" stroke="var(--bright)" stroke-width=".6"/></svg>baumpflege-vehmar.de</div>
  </div>
</section>

<section class="card col-right row-3">
  <div class="rule" style="top:81px"></div>
  <div class="brand brand--band brand--green"><span class="brand__mark"></span>Baumpflege Vehmar</div>
  <div class="rule" style="top:106px"></div>
  <ul class="services services--wide">
    <li>Neupflanzungen</li>
    <li>Herstellung der Verkehrssicherheit von Bäumen</li>
    <li>Kronenrückschnitt (Einkürzung &amp; Kronenpflege)</li>
    <li>Prüfung von Bäumen auf Standsicherheit</li>
    <li>Fällung von Bäumen</li>
    <li>Obstbaumschnitt</li>
    <li>Wurzelstockfräsen</li>
  </ul>
</section>

</body>
</html>
```